NZ First of it's kind solutions directory and marketplace for busy Mums needs a business card design

We need a business card design for our new nationwide business in NZ (long term plans to go global). We provide solutions to the everyday challenges that busy Mums face by connecting them with quality communities and suppliers of carefully selected, relevant products and services. We sell direct via our online marketplace. The final design should communicate our values of inclusivity, quality and smart solutions. Colours should incorporate our logo colour palette of #477077 and #6ba8b2. Our website is at https://www.brightnestmums.example

Target Market(s)

busy Mums, Age 28 – 50, female, income over $100K, location main centres NZ primarily but NZ wide. Is likely juggling work or career with a young family. Probably had hobbies which have fallen by the wayside.
-Wants to succeed in her chosen career without compromising on family life
-to successfully juggle her career without feeling like she is compromising her children
- Is time poor, something always has to give and it’s generally her health (she’ll stay up late, get stressed)
- probably ex corporate or professional career. Has discretional income

Industry/Entity Type

Business

Contact Information for Business Card

Lena Forbisher, Founder, BrightNestMums.example (Strapline Tap; Gather; Sorted), 47 Kowhai Terrace, Ellerslie, Auckland 1051, New Zealand. Mob: 021 483 517 Ph: +64 (0)9 571 4860

Font styles to use
Other font styles liked:
• Raleway, and/or Architects Daughter

Colors
00a990
33b8a4
86cfc6
cfeae6

Requirements
Must have
• the above details, streamline. the logo and colours associated with those logos
Should not have
• foil or metallic colours

```html
<!DOCTYPE html>
<html lang="en">
<head>
<meta charset="utf-8">
<title>BrightNestMums business card</title>
<link href="https://fonts.googleapis.com/css2?family=Oswald:wght@500&family=Work+Sans:wght@400;600&display=swap" rel="stylesheet">
<style>
  :root {
    --backdrop: #2a2a2b;
    --card: #1c1c1d;
    --card-sheen: #2c2c2e;
    --teal-dark: #477077;
    --teal-light: #6ba8b2;
    --accent-strip: #3db3d0;
    --text-light: #f2f2f2;
    --text-muted: #d8d8d8;
  }
  * { box-sizing: border-box; margin: 0; padding: 0; }
  html, body {
    width: 1200px; height: 900px; overflow: hidden;
    background: var(--backdrop);
  }
  .canvas { position: relative; width: 1200px; height: 900px; }
  .card {
    position: absolute; left: 240px; width: 720px; height: 390px;
    background: radial-gradient(ellipse at 70% 40%, var(--card-sheen), var(--card) 70%);
    border-bottom: 7px solid var(--accent-strip);
    box-shadow: 0 14px 30px rgba(0,0,0,0.45);
  }
  .card--front { top: 45px; }
  .card--back { top: 465px; }

  .brand {
    position: absolute; left: 0; right: 0; top: 150px;
    display: flex; align-items: center; justify-content: center; gap: 16px;
  }
  .brand__dot {
    width: 40px; height: 40px; border-radius: 50%;
    background: var(--teal-dark);
  }
  .brand__name {
    font-family: "Work Sans", sans-serif; font-weight: 600;
    font-size: 46px; color: var(--teal-light); letter-spacing: -0.5px;
  }

  .identity {
    position: absolute; right: 400px; top: 150px; text-align: right;
  }
  .identity__name {
    font-family: "Oswald", sans-serif; font-weight: 500;
    font-size: 40px; line-height: 1; color: var(--teal-light);
    text-transform: uppercase; letter-spacing: 0.5px;
  }
  .identity__role {
    font-family: "Work Sans", sans-serif; font-size: 17px;
    color: var(--text-muted); letter-spacing: 1px; margin-top: 4px;
  }
  .divider {
    position: absolute; left: 338px; top: 150px; width: 2px; height: 62px;
    background: var(--text-light);
  }
  .contacts {
    position: absolute; left: 362px; top: 150px;
    list-style: none;
    font-family: "Work Sans", sans-serif; font-size: 17px;
    color: var(--text-light); letter-spacing: 1px;
  }
  .contacts li { display: flex; align-items: center; gap: 8px; height: 21px; }
  .contacts svg { width: 12px; height: 12px; fill: var(--teal-light); flex: none; }
  .address {
    position: absolute; left: 70px; bottom: 42px;
    display: flex; align-items: center; gap: 12px;
    font-family: "Work Sans", sans-serif; font-size: 18px;
    color: var(--text-light); letter-spacing: 1.2px;
  }
  .address svg { width: 14px; height: 18px; fill: var(--text-light); }
</style>
</head>
<body>
<main class="canvas">
  <section class="card card--front" aria-label="Card front">
    <div class="brand">
      <span class="brand__dot"></span>
      <span class="brand__name">BrightNestMums</span>
    </div>
  </section>

  <section class="card card--back" aria-label="Card back">
    <div class="identity">
      <h1 class="identity__name">Lena Forbisher</h1>
      <p class="identity__role">Founder</p>
    </div>
    <div class="divider"></div>
    <ul class="contacts">
      <li>
        <svg viewBox="0 0 12 12" aria-hidden="true"><path d="M3 0h6a1 1 0 0 1 1 1v10a1 1 0 0 1-1 1H3a1 1 0 0 1-1-1V1a1 1 0 0 1 1-1zm0 1.5v8h6v-8z"/></svg>
        021 483 517
      </li>
      <li>
        <svg viewBox="0 0 12 12" aria-hidden="true"><path d="M2.5 0.5l2 2-1 1.5c.8 1.7 2 2.9 3.5 3.6l1.5-1 2 2-1.2 2C5 10.4 1.6 7 .5 1.7z"/></svg>
        +64 (0)9 571 4860
      </li>
      <li>
        <svg viewBox="0 0 12 12" aria-hidden="true"><path d="M6 0a6 6 0 1 0 0 12A6 6 0 0 0 6 0zm0 1.2c.7.8 1.2 2 1.4 3.3H4.6C4.8 3.2 5.3 2 6 1.2zM1.3 5.5h2.3c0 .4 0 .7.1 1H1.3a4.7 4.7 0 0 1 0-1zm3.3 0h2.8a7 7 0 0 1 0 1H4.6a7 7 0 0 1 0-1zm3.8 0h2.3a4.7 4.7 0 0 1 0 1H8.3c.1-.3.1-.6.1-1zM4.6 7.5h2.8C7.2 8.8 6.7 10 6 10.8 5.3 10 4.8 8.8 4.6 7.5z"/></svg>
        www.brightnestmums.example
      </li>
    </ul>
    <p class="address">
      <svg viewBox="0 0 14 18" aria-hidden="true"><path d="M7 0a6 6 0 0 1 6 6c0 4-6 10-6 10S1 10 1 6a6 6 0 0 1 6-6zm0 3.5a2.5 2.5 0 1 0 0 5 2.5 2.5 0 0 0 0-5z"/></svg>
      47 Kowhai Terrace, Ellerslie Auckland 1051, New Zealand
    </p>
  </section>
</main>
</body>
</html>
```